Property management company looking for modern card design

We at Blue Heron Partners provides property management services for its residential and commercial properties, with expertise in all categories of multifamily, industrial and office projects throughout California.

We need a business card design that is professional and modern designed business card. In our field, clients get hundreds of business cards, we would like our card to stand out.

Please avoid small print.

Target Market(s)

Professionals and high end clients

Industry/Entity Type

Financial Planning

Contact Information for Business Card

Company Name: Blue Heron Partners, Name, email, license #, phone number, website blueheronpartners.com

Font styles to use
Sans Serif

Requirements
Must have
• The card design needs to be adaptable because there is a possibly we will be expanding into different sectors other than real estate. The card design should be focused on financial planning and asset management.
Nice to have
• Modern and simple business card. Eye catching. Non-standard size/shaped cards would be great.
• blueheronpartners.com
Should not have
• Too many bright color or any pictures or shapes of real estate stuff.

```html
<!DOCTYPE html>
<html lang="en">
<head>
<meta charset="utf-8">
<title>Blue Heron Partners — Business Card</title>
<link href="https://fonts.googleapis.com/css2?family=Arimo:wght@400;700&display=swap" rel="stylesheet">
<style>
  :root {
    --backdrop: #e9e6e1;
    --card: #f7f7f7;
    --card-edge: #dcdcdc;
    --brand-red: #d3213c;
    --brand-red-deep: #b8152e;
    --ink: #2b2b2b;
    --white: #ffffff;
  }
  * { box-sizing: border-box; margin: 0; padding: 0; }
  html, body {
    width: 1200px; height: 902px; overflow: hidden;
    background: var(--backdrop);
    font-family: "Arimo", Arial, sans-serif;
  }
  .canvas { position: relative; width: 1200px; height: 902px; }

  .card {
    position: absolute;
    width: 540px; height: 310px;
    background: var(--card);
    border: 1px solid var(--card-edge);
    box-shadow: 0 10px 24px rgba(0,0,0,0.18);
    overflow: hidden;
  }
  .card--front { left: 80px; top: 100px; }
  .card--back  { left: 580px; top: 490px; }

  /* brand lockup */
  .brand { display: flex; flex-direction: column; align-items: center; gap: 16px; }
  .brand-dot {
    width: 110px; height: 110px; border-radius: 50%;
    background: var(--brand-red);
  }
  .brand-name {
    color: var(--brand-red);
    font-weight: 400;
    font-size: 36px;
    letter-spacing: 6px;
    white-space: nowrap;
  }
  .card--front .brand {
    position: absolute; left: 0; right: 0; top: 62px;
  }

  /* back side */
  .card--back .brand {
    position: absolute; left: 18px; top: 52px; width: 230px; gap: 12px;
  }
  .card--back .brand-dot { width: 92px; height: 92px; }
  .card--back .brand-name { font-size: 25px; letter-spacing: 4px; }

  .divider {
    position: absolute; left: 262px; top: 28px;
    width: 1px; height: 170px; background: var(--brand-red);
  }
  .holder {
    position: absolute; left: 284px; top: 34px;
    color: var(--brand-red); font-size: 22px;
  }
  .contacts {
    position: absolute; left: 284px; top: 112px;
    list-style: none; display: flex; flex-direction: column; gap: 6px;
  }
  .contact {
    display: flex; align-items: center; gap: 10px;
    color: var(--ink); font-size: 19px;
  }
  .contact-icon {
    width: 20px; height: 20px; border-radius: 4px;
    background: var(--brand-red);
    display: flex; align-items: center; justify-content: center;
    flex: none;
  }
  .license-band {
    position: absolute; left: 0; right: 0; bottom: 0; height: 78px;
    background: linear-gradient(180deg, var(--brand-red), var(--brand-red-deep));
    display: flex; align-items: center; justify-content: center;
    color: var(--white); font-size: 19px;
  }
</style>
</head>
<body>
<main class="canvas">

  <section class="card card--front" aria-label="Card front">
    <div class="brand">
      <span class="brand-dot"></span>
      <span class="brand-name">BLUE HERON</span>
    </div>
  </section>

  <section class="card card--back" aria-label="Card back">
    <div class="brand">
      <span class="brand-dot"></span>
      <span class="brand-name">BLUE HERON</span>
    </div>
    <span class="divider"></span>
    <p class="holder">Evan Marlowe</p>
    <ul class="contacts">
      <li class="contact">
        <span class="contact-icon">
          <svg width="12" height="12" viewBox="0 0 12 12"><path d="M3 1l2 2-1 1.5a6 6 0 0 0 3.5 3.5L9 7l2 2-1.5 2A9 9 0 0 1 1 2.5z" fill="#fff"/></svg>
        </span>
        555-014-2870
      </li>
      <li class="contact">
        <span class="contact-icon">
          <svg width="12" height="10" viewBox="0 0 12 10"><rect x="0.5" y="0.5" width="11" height="9" fill="none" stroke="#fff"/><path d="M0.5 0.5l5.5 5 5.5-5" fill="none" stroke="#fff"/></svg>
        </span>
        evan@blueheron.com
      </li>
      <li class="contact">
        <span class="contact-icon">
          <svg width="12" height="12" viewBox="0 0 12 12" fill="none" stroke="#fff"><circle cx="6" cy="6" r="5.2"/><ellipse cx="6" cy="6" rx="2.3" ry="5.2"/><path d="M0.8 6h10.4"/></svg>
        </span>
        blueheronpartners.com
      </li>
    </ul>
    <div class="license-band">Lic : 30418852</div>
  </section>

</main>
</body>
</html>
```